Harborline Auto LLC

Car Dealer Customer Service
Address: 2874 Cresthaven Road, Maplebrook, VT 05761
web: www.harborlineautoxq.net
email: harborlineautoxq@mailnest.example
Phone: (555) 555-0148
Phone: (555) 555-0173

```html
<!DOCTYPE html>
<html lang="en">
<head>
<meta charset="utf-8">
<title>Harborline Auto – Business Card</title>
<link rel="stylesheet" href="https://fonts.googleapis.com/css2?family=Montserrat:wght@800&family=Oswald:wght@500&family=Arimo:wght@400;700&display=swap">
<style>
  :root {
    --stage: #e9ebee;
    --paper: #ffffff;
    --brand-blue: #1f7fb8;
    --card-blue-top: #2a93cf;
    --card-blue-bottom: #1a74ab;
    --accent-orange: #eeb041;
    --text-light: #ffffff;
    --emboss: rgba(255,255,255,0.08);
  }
  * { box-sizing: border-box; margin: 0; padding: 0; }
  html, body { width: 1200px; height: 1015px; overflow: hidden; background: var(--stage); }
  .canvas { position: relative; width: 1200px; height: 1015px; }

  .card {
    position: absolute;
    left: 220px;
    width: 760px;
    height: 434px;
    box-shadow: 0 8px 24px rgba(0,0,0,0.18);
  }

  /* Front */
  .card-front { top: 40px; background: var(--paper); }
  .brand-mark {
    position: absolute; left: 50%; top: 72px; transform: translateX(-50%);
    width: 120px; height: 120px; border-radius: 50%;
    background: var(--brand-blue);
  }
  .brand-name {
    position: absolute; left: 0; right: 0; top: 212px; text-align: center;
    font-family: "Montserrat", sans-serif; font-weight: 800;
    font-size: 52px; letter-spacing: 1px; color: var(--brand-blue);
  }
  .tagline-row {
    position: absolute; left: 60px; right: 60px; top: 296px;
    display: flex; align-items: center; gap: 14px;
  }
  .tagline-row .rule { flex: 1; height: 1px; background: var(--brand-blue); }
  .tagline {
    font-family: "Oswald", sans-serif; font-weight: 500;
    font-size: 25px; letter-spacing: 1.5px; color: var(--accent-orange); white-space: nowrap;
  }

  /* Back */
  .card-back {
    top: 540px;
    background: linear-gradient(180deg, var(--card-blue-top), var(--card-blue-bottom));
    color: var(--text-light);
    font-family: "Arimo", sans-serif;
    overflow: hidden;
  }
  .emboss-mark {
    position: absolute; right: 60px; top: 40px;
    width: 300px; height: 300px; border-radius: 50%;
    background: var(--emboss);
    box-shadow: inset 2px 2px 4px rgba(0,0,0,0.15), inset -2px -2px 4px rgba(255,255,255,0.12);
  }
  .person { position: absolute; left: 60px; top: 120px; }
  .person-name {
    font-weight: 700; font-size: 26px; letter-spacing: 0.5px;
    color: var(--accent-orange); text-transform: uppercase;
  }
  .person-role { font-size: 19px; margin-top: 2px; }
  .address { position: absolute; left: 96px; top: 218px; font-size: 19px; line-height: 1.3; }
  .contacts { position: absolute; left: 70px; top: 292px; list-style: none; font-size: 19px; }
  .contacts li { display: flex; align-items: center; gap: 10px; line-height: 1.35; }
  .contacts svg { width: 18px; height: 18px; flex: none; fill: none; stroke: var(--accent-orange); stroke-width: 2; }
</style>
</head>
<body>
<main class="canvas">
  <section class="card card-front">
    <div class="brand-mark" aria-hidden="true"></div>
    <h1 class="brand-name">HARBORLINE AUTO</h1>
    <div class="tagline-row">
      <span class="rule"></span>
      <p class="tagline">CAR DEALER CUSTOMER SERVICE</p>
      <span class="rule"></span>
    </div>
  </section>

  <section class="card card-back">
    <div class="emboss-mark" aria-hidden="true"></div>
    <div class="person">
      <p class="person-name">Marcus Ellery</p>
      <p class="person-role">Managing Director</p>
    </div>
    <p class="address">2874 Cresthaven Road<br>Maplebrook, VT 05761</p>
    <ul class="contacts">
      <li><svg viewBox="0 0 24 24"><path d="M5 3h4l2 5-3 2a12 12 0 0 0 6 6l2-3 5 2v4a2 2 0 0 1-2 2A17 17 0 0 1 3 5a2 2 0 0 1 2-2z"/></svg>(555) 555-0148</li>
      <li><svg viewBox="0 0 24 24"><path d="M5 3h4l2 5-3 2a12 12 0 0 0 6 6l2-3 5 2v4a2 2 0 0 1-2 2A17 17 0 0 1 3 5a2 2 0 0 1 2-2z"/></svg>(555) 555-0173</li>
      <li><svg viewBox="0 0 24 24"><circle cx="12" cy="12" r="9"/><path d="M3 12h18M12 3c3 3 3 15 0 18M12 3c-3 3-3 15 0 18"/></svg>www.harborlineautoxq.net</li>
      <li><svg viewBox="0 0 24 24"><rect x="3" y="6" width="18" height="12"/><path d="M3 6l9 7 9-7"/></svg>harborlineautoxq@mailnest.example</li>
    </ul>
  </section>
</main>
</body>
</html>
```